Black Car Limousine transportation business in Naples Florida

Always stand for my reliability and RVD stands for Love, K and M are the first initials of my children's names. It should show professionalism and a dedication to customer service. We keep our clients identities private. Show our professionalism. We are Black car Black tie company. We service transportation on a reserve basis to and from residents, airports, casinos, hotels,

Target Market(s)

It is a Private car service. High end clients. Businesses, Celebrity and athletes. Service to airports, hotels, special events.

Industry/Entity Type

Business

Contact Information for Business Card

A pearl metallic or Luster card. Standard business card size. Would like the name, Company email, show we take credit cards and phone number. Currently I don't have a website but will like to add later.

Logo Text

STEADFAST RVD TRANSPORTATION

Font styles to use
Serif

Colors
eaeaea
000000

Requirements
Must have
• Must have Company email, show we take credit cards and phone number. Currently I don't have a website but will like to add later.
Nice to have
• Would like to stay with a black and white theme. Open to some color trim.
Should not have
• Open to suggestions

```html
<!DOCTYPE html>
<html lang="en">
<head>
<meta charset="utf-8">
<title>Steadfast RVD Transportation – Business Card</title>
<link rel="stylesheet" href="https://fonts.googleapis.com/css2?family=Open+Sans:ital,wght@0,400;0,600;0,700;1,700&display=swap">
<style>
  :root {
    --backdrop: #b3b3b3;
    --card: #ffffff;
    --ink: #000000;
    --silver: #8f8f8f;
    --pearl: #eaeaea;
    --car-dark: #1a1a1a;
    --car-light: #5a5a5a;
  }
  html, body {
    margin: 0;
    padding: 0;
    width: 1105px;
    height: 1200px;
    overflow: hidden;
    background: var(--backdrop);
    font-family: "Open Sans", Arial, sans-serif;
  }
  .card {
    position: absolute;
    left: 193px;
    width: 720px;
    height: 410px;
    background: var(--card);
    overflow: hidden;
  }
  .card--front { top: 167px; }
  .card--back { top: 623px; }

  .card__wave {
    position: absolute;
    inset: 0;
    width: 720px;
    height: 410px;
  }

  .brand {
    position: absolute;
    left: 48px;
    top: 60px;
    display: flex;
    align-items: center;
    gap: 14px;
  }
  .brand__vehicle {
    width: 133px;
    height: 54px;
    border-radius: 10px 18px 6px 6px;
    background: linear-gradient(180deg, var(--car-light), var(--car-dark) 55%, var(--ink));
  }
  .brand__name {
    width: 200px;
    font-weight: 700;
    font-size: 17px;
    line-height: 1.15;
    letter-spacing: 1px;
    color: var(--silver);
  }

  .contact {
    position: absolute;
    right: 50px;
    top: 206px;
    text-align: right;
    color: var(--card);
  }
  .contact__name {
    margin: 0;
    font-size: 25px;
    font-weight: 600;
    letter-spacing: 0.5px;
    line-height: 1.2;
  }
  .contact__title {
    margin: 0 0 22px;
    font-size: 19px;
    line-height: 1.2;
  }
  .contact__list {
    list-style: none;
    margin: 0;
    padding: 0;
    font-size: 18px;
    line-height: 27px;
  }
  .contact__item {
    display: flex;
    justify-content: flex-end;
    align-items: center;
    gap: 12px;
  }
  .contact__icon { width: 17px; height: 17px; flex: none; }

  .hero-vehicle {
    position: absolute;
    left: 152px;
    top: 130px;
    width: 387px;
    height: 160px;
    border-radius: 40px 60px 18px 18px;
    background: linear-gradient(180deg, var(--car-light) 0%, var(--car-dark) 45%, var(--ink) 100%);
  }
  .payment-note {
    position: absolute;
    left: 0;
    right: 0;
    top: 334px;
    display: flex;
    justify-content: center;
    align-items: center;
    gap: 10px;
    font-size: 19px;
    font-weight: 700;
    font-style: italic;
    color: var(--ink);
  }
  .payment-note__icon { width: 30px; height: 20px; }
</style>
</head>
<body>

<section class="card card--front">
  <svg class="card__wave" viewBox="0 0 720 410" aria-hidden="true">
    <path fill="var(--silver)" d="M0,238 C120,300 230,350 330,318 C430,288 480,136 580,98 C640,78 690,84 720,90 L720,410 L0,410 Z"/>
    <path fill="var(--ink)" stroke="var(--card)" stroke-width="5" d="M-5,282 C120,330 230,362 330,334 C430,304 480,152 580,112 C640,90 690,94 725,100 L725,415 L-5,415 Z"/>
  </svg>

  <div class="brand">
    <div class="brand__vehicle" role="img" aria-label="Photo of a black luxury SUV"></div>
    <div class="brand__name">STEADFAST RVD TRANSPORTATION</div>
  </div>

  <div class="contact">
    <h1 class="contact__name">DANIEL REYES</h1>
    <p class="contact__title">CEO/Founder</p>
    <ul class="contact__list">
      <li class="contact__item">555 201 7384
        <svg class="contact__icon" viewBox="0 0 24 24" aria-hidden="true"><path fill="var(--card)" d="M6.6 10.8a15.1 15.1 0 0 0 6.6 6.6l2.2-2.2c.3-.3.7-.4 1-.2 1.1.4 2.3.6 3.6.6.6 0 1 .4 1 1V20c0 .6-.4 1-1 1C10.6 21 3 13.4 3 4c0-.6.4-1 1-1h3.5c.6 0 1 .4 1 1 0 1.3.2 2.5.6 3.6.1.3 0 .7-.2 1z"/></svg>
      </li>
      <li class="contact__item">reserve@rvdcars.com
        <svg class="contact__icon" viewBox="0 0 24 24" aria-hidden="true"><rect x="2" y="5" width="20" height="14" fill="var(--card)"/><path d="M2 5l10 8 10-8" fill="none" stroke="var(--ink)" stroke-width="1.6"/></svg>
      </li>
      <li class="contact__item">www.rvdcars.com
        <svg class="contact__icon" viewBox="0 0 24 24" aria-hidden="true"><circle cx="12" cy="12" r="10" fill="var(--card)"/><path d="M8 6c2 1 3 3 2 5s-3 1-3 4M14 14c2-1 4 0 4 2" fill="none" stroke="var(--ink)" stroke-width="2"/></svg>
      </li>
    </ul>
  </div>
</section>

<section class="card card--back">
  <div class="hero-vehicle" role="img" aria-label="Photo of a black luxury SUV, side three-quarter view"></div>
  <p class="payment-note">
    <svg class="payment-note__icon" viewBox="0 0 30 20" aria-hidden="true"><rect x="1" y="1" width="28" height="18" rx="3" fill="var(--ink)"/><rect x="1" y="5" width="28" height="3" fill="var(--card)"/><rect x="5" y="12" width="8" height="3" fill="var(--card)"/></svg>
    We accept credit cards
  </p>
</section>

</body>
</html>
```